Label for kQm Ranch beef tallow

I need a small label to go on a 2oz amber glass jar as well as a 4 oz. amber glass jar of moisturizer.
I prefer it to be rectangular for the 2oz jar since it's small and square for the 4oz jar.
I'd like to keep our kQm Ranch logo the same font and style, which is attached. Ten Sleep, Wyoming should be left out. The font for kQm Ranch is spartan.
The label content is as follows:
Heritage Tallow
Whipped Moisturizer
Ingredients: Beef Tallow, jojoba oil, peppermint oil.
2oz. jar

Instead of a white label, I'm thinking of a tan or brown label that will blend in with the amber jar. The lettering could then be a white, cream or even rust/burgandy color. Something to give it a rich look.

Thank you!

Target Market(s)

Mainly women but men as well.

Industry/Entity Type

Ranching and online beef sales

Requirements
Must have
• kQm Ranch logo

```html
<!DOCTYPE html>
<html lang="en">
<head>
<meta charset="UTF-8">
<title>kQm Ranch – Heritage Tallow Labels</title>
<link rel="stylesheet" href="https://fonts.googleapis.com/css2?family=League+Spartan:wght@400;500;600&family=Whisper&display=swap">
<style>
  :root {
    --backdrop: #e6e6e6;
    --label: #ffffff;
    --ink: #111111;
  }
  * { margin: 0; padding: 0; box-sizing: border-box; }
  html, body {
    width: 1200px;
    height: 1200px;
    overflow: hidden;
    background: var(--backdrop);
  }
  .sheet {
    width: 1200px;
    height: 1200px;
    display: flex;
    align-items: center;
    justify-content: center;
    gap: 60px;
  }
  .label {
    background: var(--label);
    color: var(--ink);
    font-family: "League Spartan", sans-serif;
    display: flex;
    flex-direction: column;
    align-items: center;
    text-align: center;
    position: relative;
  }
  .label--small {
    width: 500px;
    height: 270px;
    border-radius: 36px;
    justify-content: center;
    padding-left: 50px;
  }
  .label--large {
    width: 500px;
    height: 500px;
    border-radius: 36px;
    justify-content: space-between;
    padding: 40px 30px 36px;
  }
  .line-name {
    font-family: "Whisper", cursive;
    font-weight: 400;
    line-height: 1;
    white-space: nowrap;
  }
  .label--small .line-name {
    position: absolute;
    left: 56px;
    top: 50%;
    font-size: 38px;
    transform: translate(-50%, -50%) rotate(-90deg);
  }
  .label--large .line-name { font-size: 50px; }
  .brand {
    font-weight: 400;
    letter-spacing: 0.5px;
    line-height: 1;
  }
  .label--small .brand { font-size: 52px; margin-bottom: 22px; }
  .label--large .brand { font-size: 72px; }
  .details {
    display: flex;
    flex-direction: column;
    align-items: center;
  }
  .product {
    font-weight: 500;
    line-height: 1;
  }
  .label--small .product { font-size: 22px; margin-bottom: 6px; }
  .label--large .product { font-size: 32px; margin-bottom: 10px; }
  .ingredients {
    font-weight: 500;
    line-height: 1.2;
  }
  .label--small .ingredients { font-size: 12px; margin-bottom: 14px; }
  .label--large .ingredients { font-size: 18px; margin-bottom: 24px; }
  .net-weight {
    font-weight: 600;
    line-height: 1;
  }
  .label--small .net-weight { font-size: 12px; }
  .label--large .net-weight { font-size: 17px; }
</style>
</head>
<body>
  <main class="sheet">
    <section class="label label--small" aria-label="2 oz jar label">
      <p class="line-name">Heritage Tallow</p>
      <h2 class="brand">kQm Ranch</h2>
      <div class="details">
        <h3 class="product">WHIPPED MOISTURIZER</h3>
        <p class="ingredients">Beef Tallow, jojoba oil, peppermint oil</p>
        <p class="net-weight">2oz.</p>
      </div>
    </section>
    <section class="label label--large" aria-label="4 oz jar label">
      <p class="line-name">Heritage Tallow</p>
      <h2 class="brand">kQm Ranch</h2>
      <div class="details">
        <h3 class="product">WHIPPED MOISTURIZER</h3>
        <p class="ingredients">Beef Tallow, jojoba oil, peppermint oil</p>
        <p class="net-weight">4oz.</p>
      </div>
    </section>
  </main>
</body>
</html>
```